MRT Property - Business Cards

Looking for a business card & general letterhead, signage etc design for our new logo.

Colours:
000a20
0056a2
00b5ef
0088ce
68cef2

Fonts:
Poppins
Karla

Please keep look and feel of new brand - example in the zip package I sent.

```html
<!DOCTYPE html>
<html lang="en">
<head>
<meta charset="utf-8">
<title>MRT Property – Business Cards</title>
<link rel="stylesheet" href="https://fonts.googleapis.com/css2?family=Karla:wght@400;500&family=Poppins:wght@500;600;700&display=swap">
<style>
  :root {
    --navy: #000a20;
    --card-dark: #0b1120;
    --royal: #0056a2;
    --cyan: #00b5ef;
    --sky: #0088ce;
    --ice: #68cef2;
    --white: #ffffff;
    --stage: #242424;
  }
  * { box-sizing: border-box; margin: 0; padding: 0; }
  html, body {
    width: 1200px; height: 781px; overflow: hidden;
    background: var(--stage);
  }
  .canvas { position: relative; width: 1200px; height: 781px; }

  .card {
    position: absolute;
    width: 540px; height: 310px;
    border-radius: 18px;
    border: 3px solid var(--cyan);
    overflow: hidden;
    box-shadow: 0 14px 30px rgba(0,0,0,.45);
  }

  /* Front */
  .card--front {
    left: 60px; top: 60px;
    background: var(--sky);
    display: flex; align-items: center; justify-content: center;
  }
  .brand {
    display: flex; align-items: center; gap: 16px;
    font-family: "Poppins", sans-serif; font-weight: 700;
    color: var(--white);
  }
  .brand__dot { width: 22px; height: 22px; border-radius: 50%; background: currentColor; }
  .card--front .brand { font-size: 52px; letter-spacing: .5px; }

  /* Back */
  .card--back {
    left: 600px; top: 411px;
    background: var(--card-dark);
  }
  .card--back .brand {
    position: absolute; left: 34px; top: 40px;
    font-size: 30px; color: var(--royal); gap: 12px;
  }
  .card--back .brand__dot { width: 16px; height: 16px; background: var(--ice); }

  .person {
    position: absolute; right: 34px; top: 44px;
    text-align: right;
  }
  .person__name {
    font-family: "Poppins", sans-serif; font-weight: 600;
    font-size: 20px; letter-spacing: 1px;
    color: var(--royal); text-transform: uppercase;
  }
  .person__role {
    font-family: "Karla", sans-serif; font-size: 14px;
    color: var(--white); margin-top: 2px;
  }
  .person__bar {
    position: absolute; right: 0; top: 44px;
    width: 14px; height: 44px; background: var(--royal);
  }

  .contact {
    position: absolute; left: 34px; bottom: 28px;
    font-family: "Karla", sans-serif; font-size: 14px;
    color: var(--white); line-height: 1.45;
  }
  .contact__address { margin-bottom: 18px; padding-left: 26px; }
  .contact__list { list-style: none; }
  .contact__item { display: flex; align-items: center; gap: 10px; }
  .contact__icon { width: 16px; height: 16px; flex: none; }
</style>
</head>
<body>
<main class="canvas">

  <section class="card card--front" aria-label="Business card front">
    <div class="brand"><span class="brand__dot"></span><span>MRT Property</span></div>
  </section>

  <section class="card card--back" aria-label="Business card back">
    <div class="brand"><span class="brand__dot"></span><span>MRT Property</span></div>

    <div class="person">
      <p class="person__name">Daniel Hart</p>
      <p class="person__role">Managing Director</p>
    </div>
    <span class="person__bar"></span>

    <div class="contact">
      <p class="contact__address">Your address, City<br>State, Zip 1234</p>
      <ul class="contact__list">
        <li class="contact__item">
          <svg class="contact__icon" viewBox="0 0 16 16" aria-hidden="true"><path fill="#68cef2" d="M3.5 1.5l2.4 2.6-1.3 1.7c.9 2 2.6 3.7 4.6 4.6l1.7-1.3 2.6 2.4-1.3 2.2C7 13.3 2.7 9 1.3 2.8z"/></svg>
          <span>123 456 789</span>
        </li>
        <li class="contact__item">
          <svg class="contact__icon" viewBox="0 0 16 16" aria-hidden="true"><rect x="1.5" y="3.5" width="13" height="9" rx="1" fill="none" stroke="#68cef2" stroke-width="1.6"/><path d="M2 4.5l6 4.5 6-4.5" fill="none" stroke="#68cef2" stroke-width="1.6"/></svg>
          <span>info@yourgmail.com</span>
        </li>
        <li class="contact__item">
          <svg class="contact__icon" viewBox="0 0 16 16" aria-hidden="true"><circle cx="8" cy="8" r="6.5" fill="none" stroke="#68cef2" stroke-width="1.6"/><path d="M1.5 8h13M8 1.5c2.2 2 2.2 11 0 13M8 1.5c-2.2 2-2.2 11 0 13" fill="none" stroke="#68cef2" stroke-width="1.2"/></svg>
          <span>www.yourwebsite.com</span>
        </li>
      </ul>
    </div>
  </section>

</main>
</body>
</html>
```